Packaging design for a reclosable bag for our product

We have a logo, and we need to put it on packaging for our product and while we want the look to be simple, we want it to follow good design principles and also contain spaces for other product descriptions.

There will be 5 sizes at launch so I'd like 5 variations, one for each size.

I've included a few mockups of the type of bag that I made but they are all just rough ideas that I had.

I want the brand to look scientific and methodical and even a bit quirky, as in "wow this is a serious product but also a bit unusual."

```html
<!DOCTYPE html>
<html lang="en">
<head>
<meta charset="utf-8">
<title>VEO Bias Lighting – 5m Pouch Fronts</title>
<link rel="stylesheet" href="https://fonts.googleapis.com/css2?family=Montserrat:wght@500;700&family=Varela+Round&family=Playfair+Display:ital@1&display=swap">
<style>
  :root {
    --backdrop: #e6e6e6;
    --pouch-light: #6f6f6f;
    --pouch-dark: #363636;
    --pouch-base: #050505;
    --band: #ffffff;
    --ink: #111111;
    --paper: #ffffff;
    --chrome-light: #f4f4f4;
    --chrome-dark: #7a7a7a;
  }
  * { margin: 0; padding: 0; box-sizing: border-box; }
  html, body { width: 1200px; height: 853px; overflow: hidden; }
  body {
    background: var(--backdrop);
    font-family: "Montserrat", sans-serif;
    position: relative;
  }
  .pouch {
    position: absolute;
    top: 98px;
    width: 400px;
    height: 525px;
    overflow: hidden;
    color: var(--paper);
  }
  .pouch--bold { left: 186px; }
  .pouch--classic { left: 644px; }

  .pouch__top {
    position: absolute;
    inset: 0 0 229px 0;
  }
  .pouch--bold .pouch__top { background: linear-gradient(180deg, #7a7a7a 0%, var(--pouch-light) 60%, #5c5c5c 100%); }
  .pouch--classic .pouch__top { background: linear-gradient(180deg, #424242 0%, var(--pouch-dark) 60%, #2a2a2a 100%); }

  .pouch__zip {
    position: absolute;
    left: 38px; right: 38px; top: 58px;
    height: 6px;
    border: 1px solid rgba(255,255,255,0.18);
    border-radius: 3px;
  }

  .brand-name {
    position: absolute;
    left: 0; right: 0;
    text-align: center;
    font-family: "Montserrat", sans-serif;
    font-weight: 700;
    color: var(--paper);
    letter-spacing: -4px;
    line-height: 1;
  }
  .pouch--bold .brand-name { top: 112px; font-size: 150px; }
  .pouch--classic .brand-name { top: 84px; font-size: 160px; }

  .pouch__band {
    position: absolute;
    left: 0; right: 0;
    top: 256px;
    height: 40px;
    background: var(--band);
    border-top: 3px solid var(--pouch-base);
    border-bottom: 3px solid var(--pouch-base);
    color: var(--ink);
    font-weight: 500;
    font-size: 27px;
    letter-spacing: 1px;
    text-align: center;
    line-height: 34px;
  }

  .pouch__base {
    position: absolute;
    left: 0; right: 0; bottom: 0;
    height: 229px;
    background: radial-gradient(ellipse at 50% 40%, #1c1c1c 0%, var(--pouch-base) 75%);
    text-align: center;
  }

  .size-tag {
    position: absolute;
    font-weight: 500;
    letter-spacing: 1px;
  }
  .pouch--bold .size-tag {
    left: 182px; top: 22px;
    width: 112px; height: 16px;
    font-size: 12px; line-height: 16px;
    border-radius: 3px;
    background: linear-gradient(90deg, #8a8a8a, #3a3a3a);
  }
  .pouch--classic .size-tag {
    left: 0; right: 0; top: 46px;
    font-size: 14px;
  }

  .size-value {
    position: absolute;
    left: 0; right: 0;
    line-height: 1;
  }
  .pouch--bold .size-value {
    top: 10px;
    font-family: "Varela Round", sans-serif;
    font-size: 132px;
    letter-spacing: -4px;
    background: linear-gradient(90deg, var(--chrome-light) 0%, #d8d8d8 45%, var(--chrome-dark) 70%, #e0e0e0 100%);
    -webkit-background-clip: text;
    background-clip: text;
    color: transparent;
  }
  .pouch--classic .size-value {
    top: 74px;
    font-family: "Playfair Display", serif;
    font-style: italic;
    font-size: 64px;
    background: linear-gradient(90deg, var(--chrome-light) 0%, var(--chrome-light) 50%, var(--chrome-dark) 75%, #d0d0d0 100%);
    -webkit-background-clip: text;
    background-clip: text;
    color: transparent;
  }

  .spec-lines {
    position: absolute;
    left: 0; right: 0;
    font-weight: 500;
    font-size: 12.5px;
    line-height: 18px;
    letter-spacing: 0.3px;
  }
  .pouch--bold .spec-lines { top: 124px; }
  .pouch--classic .spec-lines { top: 157px; font-size: 13.5px; line-height: 20px; }
</style>
</head>
<body>

  <section class="pouch pouch--bold" aria-label="Pouch front, bold variant">
    <div class="pouch__top">
      <div class="pouch__zip"></div>
      <div class="brand-name">VEO</div>
    </div>
    <div class="pouch__band">BIAS LIGHTING</div>
    <div class="pouch__base">
      <div class="size-tag">EXTRA LARGE</div>
      <div class="size-value">5m</div>
      <p class="spec-lines">6500K White Bias Lighting<br>Simulated D65 CRI 90+</p>
    </div>
  </section>

  <section class="pouch pouch--classic" aria-label="Pouch front, classic variant">
    <div class="pouch__top">
      <div class="pouch__zip"></div>
      <div class="brand-name">VEO</div>
    </div>
    <div class="pouch__band">BIAS LIGHTING</div>
    <div class="pouch__base">
      <div class="size-tag">EXTRA LARGE</div>
      <div class="size-value">5m</div>
      <p class="spec-lines">6500K White Bias Lighting<br>Simulated D65 CRI 90+</p>
    </div>
  </section>

</body>
</html>
```